Your After-Marriage Lantern: Sensible, Everyday Guidance for the Freshly Solo

I need a wraparound book cover design for a ~132-page workbook. Trim size will be 8.5x11 and the book will be on 60# paper. The name of this project is the name and subtitle of the book. Here's the synopsis I've come up with, which should be included on the back cover (without the quote marks):
"So you're divorced. What do you do now? There are probably a whole bunch of
things you never thought of, like:
- Cleaning up and automating your finances
- Making sure your insurance coverages are all correct
- Removing your former spouse's name from your assets and liabilities
- Building your personal team of financial advisors
Are you aware you need to take care of these things, but you don't know where to
start? This workbook is perfect for you. You'll be led, step by step, through detailed
explanations of how to do everything on this list, and much, much more!"
Here's the author bio for the back cover:
"Gordon T. Whitlock, Esq. graduated from Halvern College School of Law in 2002 and has been a practicing trial lawyer in the Metro Atlanta area ever since. Family law has always been a big part of Gordy's practice. Throughout his career, Gordy has helped hundreds of people through their divorce cases, and now through this book, Gordy looks forward to being able to help them after the dust settles."
I have an ISBN bar code ready to go, so leave space for it on the back cover in the bottom right corner (winner will be expected to add the bar code graphic to the finished product).
This will be a print-on-demand book through Brixo's PressNook. They have a sizing template if you want to grab it for yourself.
Primarily divorced women, especially middle-aged and older

```html
<!DOCTYPE html>
<html lang="en">
<head>
<meta charset="utf-8">
<title>Your After-Marriage Lantern – Wraparound Cover</title>
<link rel="stylesheet" href="https://fonts.googleapis.com/css2?family=Bebas+Neue&family=Open+Sans:wght@400;600&display=swap">
<style>
  :root {
    --paper: #ebebe7;
    --orange: #f15a22;
    --teal: #3397a8;
    --ink: #3f4347;
    --body: #3a3d40;
    --art-light: #dedbd2;
    --art-dark: #aaa38e;
  }
  html, body {
    margin: 0;
    padding: 0;
    width: 1200px;
    height: 763px;
    overflow: hidden;
    background: var(--paper);
  }
  .cover {
    position: relative;
    width: 1200px;
    height: 763px;
    overflow: hidden;
    background: var(--paper);
    font-family: "Open Sans", Arial, sans-serif;
    color: var(--body);
  }
  .title-block {
    position: absolute;
    margin: 0;
    text-align: center;
    font-family: "Bebas Neue", "Arial Narrow", sans-serif;
    font-weight: 400;
    line-height: 1;
  }
  .title-block .kicker { color: var(--orange); display: block; }
  .title-block .main {
    color: var(--teal);
    display: block;
    text-shadow: 0 2px 3px rgba(0,0,0,0.25);
  }
  .title-block .subtitle { color: var(--ink); display: block; }

  .back-title { left: 46px; width: 507px; top: 26px; }
  .back-title .kicker { font-size: 30px; }
  .back-title .main { font-size: 84px; margin-top: -6px; }
  .back-title .subtitle { font-size: 20px; margin-top: -4px; }

  .front-title { left: 660px; width: 490px; top: 24px; }
  .front-title .kicker { font-size: 56px; }
  .front-title .main { font-size: 152px; margin-top: -12px; letter-spacing: 1px; }
  .front-title .subtitle { font-size: 33px; line-height: 1.02; margin-top: -20px; }

  .synopsis {
    position: absolute;
    left: 46px;
    top: 196px;
    width: 507px;
    font-size: 14.6px;
    line-height: 19.5px;
    text-align: justify;
  }
  .synopsis p { margin: 0; }
  .checklist {
    list-style: none;
    margin: 18px 0 17px;
    padding: 0;
  }
  .checklist li {
    position: relative;
    padding-left: 22px;
  }
  .checklist li svg {
    position: absolute;
    left: 5px;
    top: 4px;
  }
  .art {
    position: absolute;
    border-radius: 50%;
    background: radial-gradient(ellipse at 40% 40%, var(--art-light), var(--art-dark));
  }
  .art-back { left: 252px; top: 430px; width: 86px; height: 92px; }
  .art-front { left: 760px; top: 305px; width: 290px; height: 365px; }
  .bio {
    position: absolute;
    left: 46px;
    top: 535px;
    width: 507px;
    margin: 0;
    font-size: 12.3px;
    line-height: 17.3px;
    text-align: justify;
  }
  .author-name {
    position: absolute;
    left: 690px;
    width: 440px;
    top: 705px;
    margin: 0;
    text-align: center;
    font-family: "Bebas Neue", "Arial Narrow", sans-serif;
    font-size: 40px;
    letter-spacing: 2px;
    color: var(--ink);
    font-weight: 400;
  }
</style>
</head>
<body>
<div class="cover">
  <section class="back-cover">
    <h2 class="title-block back-title">
      <span class="kicker">Your After-Marriage</span>
      <span class="main">Lantern</span>
      <span class="subtitle">Sensible, Everyday Guidance for the Freshly Solo</span>
    </h2>

    <div class="synopsis">
      <p>So you're divorced. What do you do now? There are probably a whole bunch of things you never thought of, like:</p>
      <ul class="checklist">
        <li><svg width="11" height="11" viewBox="0 0 11 11"><circle cx="5.5" cy="5.5" r="4.5" fill="#9a9a92"/><path d="M3 8 L8 3" stroke="#e04a2a" stroke-width="1.6"/></svg>Cleaning up and automating your finances</li>
        <li><svg width="11" height="11" viewBox="0 0 11 11"><circle cx="5.5" cy="5.5" r="4.5" fill="#9a9a92"/><path d="M3 8 L8 3" stroke="#e04a2a" stroke-width="1.6"/></svg>Making sure your insurance coverages are all correct</li>
        <li><svg width="11" height="11" viewBox="0 0 11 11"><circle cx="5.5" cy="5.5" r="4.5" fill="#9a9a92"/><path d="M3 8 L8 3" stroke="#e04a2a" stroke-width="1.6"/></svg>Removing your former spouse's name from your assets and liabilities</li>
        <li><svg width="11" height="11" viewBox="0 0 11 11"><circle cx="5.5" cy="5.5" r="4.5" fill="#9a9a92"/><path d="M3 8 L8 3" stroke="#e04a2a" stroke-width="1.6"/></svg>Building your personal team of financial advisors</li>
      </ul>
      <p>Are you aware you need to take care of these things, but you don't know where to start? This workbook is perfect for you. You'll be led, step by step, through detailed explanations of how to do everything on this list, and much, much more!</p>
    </div>

    <div class="art art-back" role="img" aria-label="Small photo of an open brass and silver pocket compass"></div>

    <p class="bio">Gordon T. Whitlock, Esq. graduated from Halvern College School of Law in 2002 and has been a practicing trial lawyer in the Metro Atlanta area ever since. Family law has always been a big part of Gordy's practice. Throughout his career, Gordy has helped hundreds of people through their divorce cases, and now through this book, Gordy looks forward to being able to help them after the dust settles.</p>
  </section>

  <section class="front-cover">
    <h1 class="title-block front-title">
      <span class="kicker">Your After-Marriage</span>
      <span class="main">Lantern</span>
      <span class="subtitle">Sensible, Everyday Guidance for<br>the Freshly Solo</span>
    </h1>

    <div class="art art-front" role="img" aria-label="Photo of an open silver pocket compass with raised sighting lid and red needle"></div>

    <p class="author-name">Gordon T. Whitlock, Esq.</p>
  </section>
</div>
</body>
</html>
```